We are a new company with 2 divisions a medical research and medical product sales. We need a company logo and Business Cards. The design files need to be provided to us in Adobe Photoshop CS 5.1.

Target Market(s)

Medical Community

Industry/Entity Type

Medical

Contact Information for Business Card

Company Name - Harrowgate Lifesciences LLC
Company Address 4127 Larkspur Ave Suite 7, Gainesville Fl 32614

Requirements
Must have
• The design files need to be provided to us in Adobe Photoshop CS 5.1.

```html
<!DOCTYPE html>
<html lang="en">
<head>
<meta charset="utf-8">
<title>Harrowgate Lifesciences LLC – Business Card</title>
<link rel="stylesheet" href="https://fonts.googleapis.com/css2?family=EB+Garamond:wght@400;500&display=swap">
<style>
  :root {
    --backdrop: #e7e6e4;
    --card: #ffffff;
    --brand-blue: #1f6fb8;
    --brand-green: #2bb34a;
    --ink: #2e2e2e;
    --ink-soft: #4a4a4a;
  }
  * { box-sizing: border-box; margin: 0; padding: 0; }
  html, body {
    width: 1200px; height: 900px; overflow: hidden;
    background: var(--backdrop);
  }
  .canvas {
    width: 1200px; height: 900px;
    display: flex; align-items: center; justify-content: center;
  }
  .business-card {
    position: relative;
    width: 980px; height: 560px;
    background: var(--card);
    box-shadow: 0 12px 40px rgba(0,0,0,.18);
    font-family: "EB Garamond", Garamond, serif;
    overflow: hidden;
  }
  .brand {
    position: absolute; left: 56px; top: 52px;
    display: flex; align-items: flex-start; gap: 22px;
  }
  .brand-dot {
    width: 64px; height: 64px; border-radius: 50%;
    background: var(--brand-green); flex: none; margin-top: 6px;
  }
  .brand-name {
    color: var(--brand-blue);
    font-size: 50px; font-weight: 400; line-height: .95;
    letter-spacing: .5px; text-transform: uppercase;
  }
  .contact {
    position: absolute; right: 64px; bottom: 78px;
    text-align: right; color: var(--ink);
  }
  .contact-name { font-size: 48px; line-height: 1.05; color: var(--ink-soft); }
  .contact-role { font-size: 32px; line-height: 1.1; margin-bottom: 14px; }
  .contact-line { font-size: 30px; line-height: 1.12; }
  .card-band {
    position: absolute; left: 0; right: 0; bottom: 0; height: 46px;
    display: flex;
  }
  .band-segment { height: 100%; position: relative; }
  .band-segment::after {
    content: ""; position: absolute; left: 0; right: 0; bottom: 0; height: 14px;
  }
  .band-green { width: 38%; background: linear-gradient(to bottom, rgba(43,179,74,0), rgba(43,179,74,.35)); }
  .band-green::after { background: var(--brand-green); }
  .band-blue { flex: 1; background: linear-gradient(to bottom, rgba(31,111,184,0), rgba(31,111,184,.3)); border-left: 3px solid #fff; }
  .band-blue::after { background: var(--brand-blue); }
</style>
</head>
<body>
<main class="canvas">
  <article class="business-card">
    <header class="brand">
      <span class="brand-dot" aria-hidden="true"></span>
      <h1 class="brand-name">Harrowgate<br>Lifesciences LLC.</h1>
    </header>
    <section class="contact">
      <p class="contact-name">Daniel Okafor</p>
      <p class="contact-role">Chief Executive Officer</p>
      <p class="contact-line">4127 Larkspur Ave Suite 7</p>
      <p class="contact-line">Gainesville Fl 32614</p>
      <p class="contact-line">Tel: 352 555 0147</p>
      <p class="contact-line">Email: d.okafor@harrowgatelife.com</p>
      <p class="contact-line">www.harrowgatelife.com</p>
    </section>
    <div class="card-band" aria-hidden="true">
      <span class="band-segment band-green"></span>
      <span class="band-segment band-blue"></span>
    </div>
  </article>
</main>
</body>
</html>
```